Design a "healthy, happy dog and cat" cheque/check background

I am looking for a few design concepts featuring a happy healthy dog and cat, that will be used as the background of a paper cheque/check.

This will require Photoshop and stock photos.

Here is the design brief: https://docs.plinvaro.com/document/d/4Rt8mKx2LqW9zVbN3cHy7TfJ1sDp6GaE0uYoZiXeMwnB/edit?usp=sharing

Colors

Designer to choose colors to be used in the design.

Requirements
Must have
• A happy dog and cat the main focus within the "empty" central part of the cheque/check, and a complementary background for the rest of the cheque, following the design guidelines in the attached plinvaro doc.

```html
<!DOCTYPE html>
<html lang="en">
<head>
<meta charset="utf-8">
<title>Personal Cheque – Dog and Cat</title>
<link rel="stylesheet" href="https://fonts.googleapis.com/css2?family=Arimo:wght@400;700&family=Share+Tech+Mono&display=swap">
<style>
  :root {
    --page: #ffffff;
    --cheque-tan: #cdb9a8;
    --ink: #1b1b1b;
    --ink-soft: #333333;
    --field: #ffffff;
    --rule: #2a2a2a;
    --fur-light: #f4efe9;
    --fur-warm: #d9a874;
    --fur-mid: #e9dfd6;
  }
  * { box-sizing: border-box; margin: 0; padding: 0; }
  html, body { width: 1200px; height: 544px; overflow: hidden; background: var(--page); }
  body { font-family: "Arimo", Arial, sans-serif; color: var(--ink); position: relative; }

  .cheque { position: absolute; left: 0; top: 0; width: 1192px; height: 416px; background: var(--cheque-tan); overflow: hidden; }
  .pet-photo { position: absolute; left: 0; top: 0; width: 1192px; height: 416px; }

  .abs { position: absolute; white-space: nowrap; }
  .account-name { left: 57px; top: 61px; font-size: 21px; font-weight: 700; color: #2b2b2b; }
  .account-address { left: 57px; top: 85px; font-size: 19px; line-height: 23px; color: #2b2b2b; }
  .cheque-number { left: 1022px; top: 46px; font-size: 24px; font-weight: 700; }

  .date-label { left: 783px; top: 110px; font-size: 20px; }
  .date-boxes { left: 850px; top: 91px; display: flex; gap: 3px; }
  .date-box { width: 36px; height: 35px; background: var(--field); }
  .date-format { left: 850px; top: 130px; display: flex; gap: 3px; font-size: 14px; }
  .date-format span { width: 36px; text-align: center; }

  .payee-label { left: 57px; top: 190px; font-size: 14px; line-height: 14px; }
  .rule { position: absolute; background: var(--rule); height: 1px; }
  .dollar-sign { left: 947px; top: 186px; font-size: 30px; }
  .amount-box { position: absolute; left: 973px; top: 176px; width: 193px; height: 47px; background: var(--field); }
  .amount-words { left: 920px; top: 253px; font-size: 15px; }

  .bank-mark { position: absolute; left: 64px; top: 288px; width: 78px; height: 78px; border-radius: 50%; background: #1b1b1b; }
  .bank-name { left: 153px; top: 300px; font-size: 19px; font-weight: 700; }
  .bank-address { left: 153px; top: 320px; font-size: 18px; line-height: 20px; }

  .company-name { left: 808px; top: 333px; font-size: 15px; }
  .memo-label { left: 60px; top: 382px; font-size: 12px; }

  .security-badge { position: absolute; left: 1160px; top: 270px; width: 32px; height: 137px; border: 1px solid #555; background: #d8c8ba; }

  .micr-line { left: 52px; top: 448px; font-family: "Share Tech Mono", monospace; font-size: 34px; letter-spacing: 2px; color: #111; }
</style>
</head>
<body>
  <section class="cheque">
    <svg class="pet-photo" viewBox="0 0 1192 416" role="img" aria-label="Photo of a golden puppy and a white kitten cuddling on soft white fur">
      <defs>
        <linearGradient id="fur" x1="0" y1="0" x2="1" y2="0">
          <stop offset="0" stop-color="#eee6dd"/>
          <stop offset="0.3" stop-color="#dcae7c"/>
          <stop offset="0.45" stop-color="#d6a472"/>
          <stop offset="0.6" stop-color="#f2ede8"/>
          <stop offset="1" stop-color="#ebe4de"/>
        </linearGradient>
      </defs>
      <path d="M25 160 C90 130 160 130 200 120 C230 40 270 0 330 0 L640 0 C700 20 760 60 800 110 C860 140 900 200 920 240 C940 300 970 360 985 416 L25 416 Z" fill="url(#fur)"/>
    </svg>

    <div class="abs account-name">NLVC - Brightleaf Cheques Personal Cheque</div>
    <div class="abs account-address">15 Residential Street<br>Toronto, Ontario M1M 1M1</div>
    <div class="abs cheque-number">101</div>

    <div class="abs date-label">DATE</div>
    <div class="abs date-boxes">
      <div class="date-box"></div><div class="date-box"></div><div class="date-box"></div><div class="date-box"></div>
      <div class="date-box"></div><div class="date-box"></div><div class="date-box"></div><div class="date-box"></div>
    </div>
    <div class="abs date-format"><span>D</span><span>D</span><span>M</span><span>M</span><span>Y</span><span>Y</span><span>Y</span><span>Y</span></div>

    <div class="abs payee-label">PAY TO THE<br>ORDER OF</div>
    <div class="rule" style="left:57px;top:222px;width:866px;"></div>
    <div class="rule" style="left:922px;top:190px;width:1px;height:33px;"></div>
    <div class="abs dollar-sign">$</div>
    <div class="amount-box"></div>

    <div class="rule" style="left:57px;top:276px;width:848px;"></div>
    <svg class="abs" style="left:903px;top:238px;" width="12" height="40"><line x1="2" y1="38" x2="10" y2="2" stroke="#2a2a2a" stroke-width="1"/></svg>
    <div class="abs amount-words">100 DOLLARS</div>

    <div class="bank-mark" aria-hidden="true"></div>
    <div class="abs bank-name">Your Financial Institution</div>
    <div class="abs bank-address">200 Finance Avenue<br>Your City, Your Province A1B 2CS</div>

    <div class="abs company-name">Optional Company Name</div>

    <div class="abs memo-label">MEMO</div>
    <div class="rule" style="left:60px;top:396px;width:525px;"></div>
    <div class="rule" style="left:686px;top:396px;width:412px;"></div>

    <div class="security-badge" aria-hidden="true"></div>
  </section>

  <div class="abs micr-line">⑈101⑈ ⑆12345⑉678⑆ 12345⑉6789⑈</div>
</body>
</html>
```